Core Values Banner For Hearthwell Guards Inc

We want to take the core values for our small growing chimney service company and post them for our entire team to see on a daily basis. We want to be remind everyone how important this is too us all. IntegrityWe try to be honest and accountable in all aspects of our business, as well as in our personal interactions. We do what we say we will do, when we say we will do it, and how we say we will do it.Kaizen“Change for the best”We strive to constantly grow and improve, both personally and professionally. We own up to our mistakes and strive to resolve and learn from them. We actively seek feedback from our clients and each other. We believe the most innovative ideas come when we intentionally look for them.FamilyWe are a family-owned business, and we consider everyone who works here and every one we serve to be part of the family. Being honest and genuine with each other and our customers is what sets us apart. We put ourselves in our customer’s shoes and make recommendations as if it were our chimney, our home and our family.

Font styles to use
Serif
Sans Serif

Colors
ec1f27

Requirements
Must have
• This banner will be approximately 2.5' in height and 6 to 6.5' in width.
• I would like all 3 core values and there definitions listed on the banner
• check out the feel of our marketing on our website www.hearthwellguardsnx.com

```html
<!DOCTYPE html>
<html lang="en">
<head>
<meta charset="utf-8">
<title>Hearthwell Guards Inc — Core Values Banner</title>
<link rel="stylesheet" href="https://fonts.googleapis.com/css2?family=Lato:wght@400;700;900&display=swap">
<style>
  :root {
    --brand-red: #d22140;
    --charcoal: #333333;
    --paper: #ffffff;
    --ghost: #ececec;
    --ink: #3a3a3a;
  }
  * { margin: 0; padding: 0; box-sizing: border-box; }
  html, body { width: 1200px; height: 540px; overflow: hidden; }
  body {
    background: var(--brand-red);
    font-family: "Lato", Arial, sans-serif;
    position: relative;
  }
  .banner {
    position: absolute;
    left: 60px; top: 62px;
    width: 1082px; height: 416px;
    background: var(--paper);
    box-shadow: 0 10px 14px rgba(0,0,0,0.28);
  }
  .value-card {
    position: absolute;
    top: 36px;
    width: 294px; height: 344px;
    --frame: var(--brand-red);
  }
  .value-card--integrity { left: 41px; }
  .value-card--kaizen { left: 394px; --frame: var(--charcoal); }
  .value-card--family { left: 746px; }

  .ghost-word {
    position: absolute; left: 0; top: 0;
    width: 294px; height: 344px;
    z-index: 0;
  }
  .ghost-word text {
    font-family: "Lato", Arial, sans-serif;
    font-weight: 900;
    font-size: 66px;
    fill: var(--ghost);
  }
  .frame {
    position: absolute; left: 0; top: 0;
    width: 294px; height: 344px;
    z-index: 1;
  }
  .frame rect { fill: var(--frame); }
  .chimney-motif {
    position: absolute;
    left: 119px; top: 320px;
    width: 56px; height: 36px;
    background: var(--frame);
    z-index: 1;
  }
  .value-icon {
    position: absolute;
    left: 50%; top: 40px;
    transform: translateX(-50%);
    width: 60px; height: 56px;
    z-index: 2;
  }
  .value-title {
    position: absolute;
    left: 0; right: 0; top: 104px;
    text-align: center;
    font-weight: 900;
    font-size: 36px;
    line-height: 40px;
    color: var(--brand-red);
    z-index: 2;
  }
  .value-tagline {
    position: absolute;
    left: 0; right: 0; top: 146px;
    text-align: center;
    font-weight: 700;
    font-size: 20px;
    line-height: 24px;
    color: var(--brand-red);
    z-index: 2;
  }
  .value-text {
    position: absolute;
    font-size: 10px;
    line-height: 15.6px;
    color: var(--ink);
    z-index: 2;
  }
  .value-text .line {
    display: block;
    white-space: nowrap;
    text-align: justify;
    text-align-last: justify;
  }
  .value-text .line--end { text-align: center; text-align-last: center; }
  .value-card--integrity .value-text { left: 41px; width: 212px; top: 199px; }
  .value-card--kaizen .value-text { left: 36px; width: 221px; top: 190px; }
  .value-card--family .value-text { left: 36px; width: 222px; top: 183px; }
</style>
</head>
<body>
  <main class="banner" aria-label="Hearthwell Guards Inc core values">

    <section class="value-card value-card--integrity">
      <svg class="ghost-word" viewBox="0 0 294 344" aria-hidden="true">
        <text x="15" y="62" textLength="266" lengthAdjust="spacingAndGlyphs">Integrity</text>
      </svg>
      <svg class="frame" viewBox="0 0 294 344" aria-hidden="true">
        <rect x="0" y="0" width="144" height="11"/>
        <rect x="151" y="0" width="143" height="11"/>
        <rect x="0" y="0" width="11" height="344"/>
        <rect x="283" y="0" width="11" height="344"/>
        <rect x="0" y="333" width="113" height="11"/>
        <rect x="181" y="333" width="113" height="11"/>
      </svg>
      <div class="chimney-motif" role="img" aria-label="Brick chimney motif"></div>
      <svg class="value-icon" viewBox="0 0 60 56" aria-hidden="true" fill="var(--brand-red)">
        <circle cx="30" cy="4" r="3"/>
        <rect x="28" y="6" width="4" height="40"/>
        <rect x="6" y="12" width="48" height="3" rx="1.5"/>
        <path d="M10 15 L2 32 M10 15 L18 32 M50 15 L42 32 M50 15 L58 32" stroke="var(--brand-red)" stroke-width="1.5" fill="none"/>
        <path d="M1 32 H19 A9 6 0 0 1 1 32 Z"/>
        <path d="M41 32 H59 A9 6 0 0 1 41 32 Z"/>
        <path d="M22 48 H38 L36 44 H24 Z"/>
        <rect x="18" y="48" width="24" height="4" rx="1"/>
      </svg>
      <h2 class="value-title">Integrity</h2>
      <p class="value-text">
        <span class="line">We try to be honest and accountable in all as-</span>
        <span class="line">pects of our business, as well as in our personal</span>
        <span class="line">interactions. We do what we say we will do,</span>
        <span class="line">when we say we will do it, and how we say we</span>
        <span class="line line--end">will do it.</span>
      </p>
    </section>

    <section class="value-card value-card--kaizen">
      <svg class="ghost-word" viewBox="0 0 294 344" aria-hidden="true">
        <text x="14" y="328" textLength="266" lengthAdjust="spacingAndGlyphs">Kaizen</text>
      </svg>
      <svg class="frame" viewBox="0 0 294 344" aria-hidden="true">
        <rect x="0" y="0" width="144" height="11"/>
        <rect x="151" y="0" width="143" height="11"/>
        <rect x="0" y="0" width="11" height="344"/>
        <rect x="283" y="0" width="11" height="344"/>
        <rect x="0" y="333" width="113" height="11"/>
        <rect x="181" y="333" width="113" height="11"/>
      </svg>
      <div class="chimney-motif" role="img" aria-label="Brick chimney motif"></div>
      <svg class="value-icon" viewBox="0 0 60 56" aria-hidden="true">
        <g fill="none" stroke="var(--brand-red)" stroke-width="3.5">
          <path d="M8 22 A23 23 0 0 1 48 12"/>
          <path d="M52 34 A23 23 0 0 1 12 44"/>
        </g>
        <g fill="var(--brand-red)">
          <path d="M44 6 L54 16 L42 18 Z"/>
          <path d="M16 50 L6 40 L18 38 Z"/>
          <rect x="20" y="34" width="3" height="6"/>
          <rect x="25" y="31" width="3" height="9"/>
          <rect x="30" y="28" width="3" height="12"/>
          <rect x="35" y="24" width="3" height="16"/>
          <path d="M19 30 L27 24 L31 26 L38 18" stroke="var(--brand-red)" stroke-width="1.5" fill="none"/>
          <path d="M35 16 L41 15 L40 21 Z"/>
        </g>
      </svg>
      <h2 class="value-title">Kaizen</h2>
      <p class="value-tagline">“Change for the best”</p>
      <p class="value-text">
        <span class="line">We strive to constantly grow and improve, both</span>
        <span class="line">personally and professionally. We own up to our</span>
        <span class="line">mistakes and strive to resolve and learn from</span>
        <span class="line">them. We actively seek feedback from our clients</span>
        <span class="line">and each other. We believe the most innovative</span>
        <span class="line">ideas come when we intentionally look for them.</span>
      </p>
    </section>

    <section class="value-card value-card--family">
      <svg class="ghost-word" viewBox="0 0 294 344" aria-hidden="true">
        <text x="16" y="62" textLength="266" lengthAdjust="spacingAndGlyphs">Family</text>
      </svg>
      <svg class="frame" viewBox="0 0 294 344" aria-hidden="true">
        <rect x="0" y="0" width="144" height="11"/>
        <rect x="151" y="0" width="143" height="11"/>
        <rect x="0" y="0" width="11" height="344"/>
        <rect x="283" y="0" width="11" height="344"/>
        <rect x="0" y="333" width="113" height="11"/>
        <rect x="181" y="333" width="113" height="11"/>
      </svg>
      <div class="chimney-motif" role="img" aria-label="Brick chimney motif"></div>
      <svg class="value-icon" viewBox="0 0 60 56" aria-hidden="true" fill="var(--brand-red)">
        <circle cx="10" cy="14" r="6"/>
        <circle cx="30" cy="14" r="6"/>
        <circle cx="50" cy="14" r="6"/>
        <path d="M1 44 V28 Q1 22 7 22 H13 Q19 22 19 28 V44 Z"/>
        <path d="M21 44 V28 Q21 22 27 22 H33 Q39 22 39 28 V44 Z"/>
        <path d="M41 44 V28 Q41 22 47 22 H53 Q59 22 59 28 V44 Z"/>
      </svg>
      <h2 class="value-title">Family</h2>
      <p class="value-text">
        <span class="line">We are a family-owned business, and we consider</span>
        <span class="line">everyone who works here and every one we serve</span>
        <span class="line">to be part of the family. Being honest and genuine</span>
        <span class="line">with each other and our customers is what sets us</span>
        <span class="line">apart. We put ourselves in our customer’s shoes</span>
        <span class="line">and make recommendations as if it were our</span>
        <span class="line line--end">chimney, our home and our family.</span>
      </p>
    </section>

  </main>
</body>
</html>
```